FunBrixo Business Card

We need a business card design for our company. We sell construction-themed amusement rides for kids.

Contact Information for Business Card

Contact info on business card should include:
Carl Dunning
Co-Founder & COO
(833) 571-FUNBRIX
Carl@funbrixo-demo.com
www.funbrixo-demo.com

```html
<!DOCTYPE html>
<html lang="en">
<head>
<meta charset="utf-8">
<title>FunBrixo Business Card</title>
<link rel="stylesheet" href="https://fonts.googleapis.com/css2?family=Courier+Prime:wght@400;700&display=swap">
<style>
  :root {
    --stage: #2a2a2a;
    --card-yellow: #fdbe14;
    --card-white: #ffffff;
    --brand-orange: #e9652b;
    --ink: #2b2b2b;
    --accent-purple: #8a3fa6;
    --divider: #e4e4ea;
    --figure-tone-a: #f6d27a;
    --figure-tone-b: #e7a54a;
    --texture-yellow: rgba(200, 160, 60, .35);
    --texture-white: rgba(205, 205, 218, .45);
  }
  * { box-sizing: border-box; margin: 0; padding: 0; }
  html, body {
    width: 1200px;
    height: 900px;
    overflow: hidden;
    background: var(--stage);
    font-family: "Courier Prime", "Courier New", monospace;
  }
  .stage {
    width: 1200px;
    height: 900px;
    display: flex;
    flex-direction: column;
    align-items: center;
    justify-content: center;
    gap: 40px;
  }
  .card {
    width: 660px;
    height: 377px;
    position: relative;
    overflow: hidden;
    box-shadow: 0 10px 30px rgba(0,0,0,.45);
  }
  .card--front { background: var(--card-yellow); }
  .card--back { background: var(--card-white); }

  .card-texture {
    position: absolute;
    left: 0;
    width: 100%;
    z-index: 0;
  }
  .card--front .card-texture--top {
    top: 0; height: 120px;
    background: linear-gradient(180deg, var(--texture-yellow), transparent);
  }
  .card--front .card-texture--bottom {
    bottom: 0; height: 150px;
    background: linear-gradient(0deg, var(--texture-yellow), transparent);
  }
  .card--back .card-texture--top {
    top: 0; height: 110px;
    background: linear-gradient(180deg, var(--texture-white), transparent);
  }
  .card--back .card-texture--bottom {
    bottom: 0; height: 120px;
    background: linear-gradient(0deg, var(--texture-white), transparent);
  }

  .wordmark {
    position: absolute;
    z-index: 1;
    display: flex;
    align-items: center;
    gap: 8px;
    color: var(--brand-orange);
    font-weight: 700;
    letter-spacing: .5px;
  }
  .wordmark__dot {
    width: 12px;
    height: 12px;
    border-radius: 50%;
    background: var(--brand-orange);
  }
  .card--front .wordmark {
    left: 200px;
    top: 150px;
    font-size: 40px;
  }
  .card--back .wordmark {
    right: 30px;
    top: 232px;
    font-size: 30px;
  }

  .crew-illustration {
    position: absolute;
    z-index: 1;
    right: 36px;
    top: 100px;
    width: 150px;
    height: 170px;
    border-radius: 12px;
    background: linear-gradient(160deg, var(--figure-tone-a), var(--figure-tone-b));
  }

  .identity {
    position: absolute;
    z-index: 1;
    left: 150px;
    top: 200px;
    text-align: right;
    width: 190px;
  }
  .identity__name {
    color: var(--brand-orange);
    font-size: 21px;
    letter-spacing: 1.5px;
  }
  .identity__role {
    color: var(--ink);
    font-size: 13px;
    letter-spacing: 1px;
    margin-top: 4px;
  }
  .divider {
    position: absolute;
    z-index: 1;
    left: 360px;
    top: 140px;
    width: 1px;
    height: 120px;
    background: var(--divider);
  }
  .contacts {
    position: absolute;
    z-index: 1;
    left: 380px;
    top: 122px;
    list-style: none;
  }
  .contacts__item {
    display: flex;
    align-items: center;
    gap: 10px;
    color: var(--ink);
    font-size: 13px;
    letter-spacing: 1px;
    height: 24px;
  }
  .contacts__icon {
    width: 14px;
    height: 14px;
    flex: none;
  }
</style>
</head>
<body>
<main class="stage">
  <section class="card card--front" aria-label="Card front">
    <div class="card-texture card-texture--top" role="img" aria-label="Faint circuit-line background pattern"></div>
    <div class="card-texture card-texture--bottom" role="img" aria-label="Faint circuit-line background pattern"></div>
    <div class="wordmark"><span class="wordmark__dot"></span><span>FunBrixo</span></div>
    <div class="crew-illustration" role="img" aria-label="Cartoon illustration of two construction workers in hard hats"></div>
  </section>

  <section class="card card--back" aria-label="Card back">
    <div class="card-texture card-texture--top" role="img" aria-label="Faint circuit-line background pattern"></div>
    <div class="card-texture card-texture--bottom" role="img" aria-label="Faint circuit-line background pattern"></div>
    <div class="identity">
      <p class="identity__name">CARL DUNNING</p>
      <p class="identity__role">CO-FOUNDER &amp; COO</p>
    </div>
    <div class="divider"></div>
    <ul class="contacts">
      <li class="contacts__item">
        <svg class="contacts__icon" viewBox="0 0 14 14" aria-hidden="true">
          <rect x="3.5" y="1" width="7" height="12" rx="1.5" fill="none" stroke="var(--accent-purple)" stroke-width="1.5"/>
          <circle cx="7" cy="11" r=".8" fill="var(--accent-purple)"/>
        </svg>
        <span>(833) 571-FUNBRIX</span>
      </li>
      <li class="contacts__item">
        <svg class="contacts__icon" viewBox="0 0 14 14" aria-hidden="true">
          <rect x="1" y="3" width="12" height="8" fill="var(--accent-purple)"/>
          <path d="M1 3 L7 8 L13 3" fill="none" stroke="#fff" stroke-width="1"/>
        </svg>
        <span>Carl@funbrixo-demo.com</span>
      </li>
      <li class="contacts__item">
        <svg class="contacts__icon" viewBox="0 0 14 14" aria-hidden="true">
          <circle cx="7" cy="7" r="6" fill="none" stroke="var(--accent-purple)" stroke-width="1.4"/>
          <ellipse cx="7" cy="7" rx="2.6" ry="6" fill="none" stroke="var(--accent-purple)" stroke-width="1.1"/>
          <line x1="1" y1="7" x2="13" y2="7" stroke="var(--accent-purple)" stroke-width="1.1"/>
        </svg>
        <span>www.funbrixo-demo.com</span>
      </li>
    </ul>
    <div class="wordmark"><span class="wordmark__dot"></span><span>FunBrixo</span></div>
  </section>
</main>
</body>
</html>
```